Business card for law firm

Need business card for new law firm. Think confident, authoritative, conservative, but not stuffy or old-fashioned.

Contact Information for Business Card

Content for card - logo (uploaded), plus the following:

Paul Whitcombe (larger font)
Managing Partner (larger font, but not as large as name)
Level 9, 7 Ferris Lane
Sydney NSW 2000
Main Tel 02 9364 2710
Direct Tel 02 8472 3159
Email paul@qvlegal.com.au
www.qvlegal.com.au

Letterhead design should include logo plus:
Level 9, 7 Ferris Lane
Sydney NSW 2000
Tel 02 8472 3159
www.qvlegal.com.au

```html
<!DOCTYPE html>
<html lang="en">
<head>
<meta charset="utf-8">
<title>Quayvale Lawyers – Business Card</title>
<link href="https://fonts.googleapis.com/css2?family=Cinzel:wght@500&family=Open+Sans:wght@400&display=swap" rel="stylesheet">
<style>
  :root {
    --backdrop: #1d1e20;
    --paper: #ffffff;
    --navy: #0d1d58;
    --ink: #16181c;
    --plaque: #0a0a0b;
    --faint: #e3e6ed;
    --muted: #3c3f45;
    --on-navy: #ffffff;
  }
  * { box-sizing: border-box; margin: 0; padding: 0; }
  html, body { width: 1200px; height: 960px; overflow: hidden; }
  body {
    background: var(--backdrop);
    font-family: "Open Sans", Arial, sans-serif;
    position: relative;
  }
  .card {
    position: absolute;
    left: 250px;
    width: 700px;
    height: 400px;
    background: var(--paper);
    overflow: hidden;
  }
  .card--front { top: 40px; }
  .card--back  { top: 520px; }

  /* Brand lockup */
  .brand {
    display: flex;
    align-items: center;
    gap: 14px;
  }
  .brand__square {
    width: 44px; height: 44px;
    background: var(--navy);
    flex: none;
  }
  .brand__name {
    font-family: "Cinzel", Georgia, serif;
    font-weight: 500;
    font-size: 30px;
    letter-spacing: 2px;
    color: var(--ink);
    white-space: nowrap;
  }

  /* Front */
  .card--front .brand {
    position: absolute;
    top: 140px; left: 0; right: 0;
    justify-content: center;
  }
  .front__web {
    position: absolute;
    top: 218px; left: 0; right: 0;
    text-align: center;
    font-size: 15px;
    letter-spacing: 3px;
    color: var(--muted);
  }

  /* Back */
  .card--back .brand {
    position: absolute;
    top: 62px; left: 56px;
  }
  .card--back .brand__name { font-size: 26px; }
  .back__accent {
    position: absolute;
    top: 70px; left: 520px;
    width: 130px; height: 130px;
    background: var(--faint);
  }
  .back__band {
    position: absolute;
    left: 0; right: 0; bottom: 0;
    height: 170px;
    background: var(--navy);
  }
  .nameplate {
    position: absolute;
    top: 208px; left: 410px;
    width: 262px; height: 72px;
    background: var(--plaque);
    border-radius: 14px 14px 18px 18px;
    color: var(--on-navy);
    font-family: "Cinzel", Georgia, serif;
    text-align: center;
    padding-top: 12px;
  }
  .nameplate__name { font-size: 20px; letter-spacing: 1px; line-height: 26px; }
  .nameplate__role { font-size: 15px; letter-spacing: 1px; line-height: 22px; }

  .contact-list {
    position: absolute;
    top: 256px; left: 40px;
    list-style: none;
    color: var(--on-navy);
    font-size: 14px;
    line-height: 26px;
  }
  .contact-list li { display: flex; align-items: center; gap: 8px; }
  .contact-list svg { width: 12px; height: 12px; flex: none; }
  .divider {
    position: absolute;
    top: 266px; left: 250px;
    width: 1px; height: 96px;
    background: rgba(255,255,255,0.45);
  }
  .address {
    position: absolute;
    top: 296px; left: 272px;
    color: var(--on-navy);
    font-size: 15px;
    line-height: 24px;
    font-style: normal;
  }
</style>
</head>
<body>

<section class="card card--front" aria-label="Card front">
  <div class="brand">
    <span class="brand__square"></span>
    <span class="brand__name">Quayvale Lawyers</span>
  </div>
  <p class="front__web">www.qvlegal.com.au</p>
</section>

<section class="card card--back" aria-label="Card back">
  <div class="back__accent"></div>
  <div class="brand">
    <span class="brand__square"></span>
    <span class="brand__name">Quayvale Lawyers</span>
  </div>

  <div class="back__band"></div>

  <ul class="contact-list">
    <li>
      <svg viewBox="0 0 12 12"><circle cx="6" cy="6" r="5.3" fill="none" stroke="#fff" stroke-width="1.2"/><path d="M4 3.5l1.2 1-0.6 1a3.5 3.5 0 0 0 1.9 1.9l1-0.6 1 1.2-0.8 0.9A4.5 4.5 0 0 1 3.1 4.3z" fill="#fff"/></svg>
      02 9364 2710
    </li>
    <li>
      <svg viewBox="0 0 12 12"><circle cx="6" cy="6" r="5.3" fill="none" stroke="#fff" stroke-width="1.2"/><path d="M4 3.5l1.2 1-0.6 1a3.5 3.5 0 0 0 1.9 1.9l1-0.6 1 1.2-0.8 0.9A4.5 4.5 0 0 1 3.1 4.3z" fill="#fff"/></svg>
      02 8472 3159
    </li>
    <li>
      <svg viewBox="0 0 12 12"><rect x="1" y="2.5" width="10" height="7" fill="#fff"/><path d="M1 2.5l5 4 5-4" fill="none" stroke="#0d1d58" stroke-width="1"/></svg>
      paul@qvlegal.com.au
    </li>
    <li>
      <svg viewBox="0 0 12 12" fill="none" stroke="#fff" stroke-width="1"><circle cx="6" cy="6" r="5"/><ellipse cx="6" cy="6" rx="2.2" ry="5"/><path d="M1 6h10"/></svg>
      www.qvlegal.com.au
    </li>
  </ul>

  <div class="divider"></div>

  <address class="address">
    Level 9, 7 Ferris Lane<br>
    Sydney NSW 2000
  </address>

  <div class="nameplate">
    <p class="nameplate__name">Paul Whitcombe</p>
    <p class="nameplate__role">Managing Partner</p>
  </div>
</section>

</body>
</html>
```